Business Cards for a law firm

Business cards for our law firm. Use our silhoette logo and OAK PARTNERS - check our website (www.oakpartners.example)

Contact Information for Business Card

our silhouette logo, OAK PARTNERS, 800-555-0147, Dorian Pemberton, dorian@oakpartners.example

Requirements
Must have
• our silhouette logo, OAK PARTNERS, 800-555-0147, Dorian Pemberton, dorian@oakpartners.example

```html
<!DOCTYPE html>
<html lang="en">
<head>
<meta charset="utf-8">
<title>Oak Partners – Business Card</title>
<link rel="stylesheet" href="https://fonts.googleapis.com/css2?family=Montserrat:wght@400;500;700&display=swap">
<style>
  :root {
    --navy: #22306b;
    --navy-back: #24346b;
    --ink: #1b1b1f;
    --paper: #ffffff;
    --backdrop: #e3e2e4;
  }
  * { margin: 0; padding: 0; box-sizing: border-box; }
  html, body { width: 1200px; height: 1108px; overflow: hidden; }
  body {
    background: var(--backdrop);
    font-family: "Montserrat", Arial, sans-serif;
    position: relative;
  }
  .card { position: absolute; width: 777px; }
  .card-front { left: 219px; top: 50px; height: 473px; background: var(--paper); }
  .card-back { left: 217px; top: 568px; height: 457px; background: var(--navy-back); }

  .brand {
    position: absolute; left: 95px; top: 252px;
    display: flex; align-items: center; gap: 12px;
  }
  .brand-mark { width: 30px; height: 30px; background: var(--navy); }
  .brand-name {
    font-weight: 500; font-size: 20px; letter-spacing: 2.5px;
    color: var(--navy);
  }
  .divider {
    position: absolute; left: 381px; top: 182px;
    width: 2px; height: 156px; background: var(--navy);
  }
  .details { position: absolute; left: 394px; top: 180px; }
  .person-name { font-weight: 700; font-size: 30px; color: var(--navy); line-height: 1.1; }
  .person-role { font-size: 17px; color: var(--ink); margin-top: 4px; margin-bottom: 10px; }
  .contact { list-style: none; }
  .contact li {
    display: flex; align-items: center; gap: 9px;
    font-size: 18px; color: var(--ink); height: 30px;
  }
  .contact svg { width: 18px; height: 18px; fill: var(--navy); flex: none; }

  .back-name {
    position: absolute; right: 63px; top: 350px;
    font-weight: 500; font-size: 34px; letter-spacing: 4px;
    color: var(--paper);
  }
</style>
</head>
<body>
  <section class="card card-front">
    <div class="brand">
      <span class="brand-mark"></span>
      <span class="brand-name">OAK PARTNERS</span>
    </div>
    <div class="divider"></div>
    <div class="details">
      <h1 class="person-name">Dorian Pemberton</h1>
      <p class="person-role">Lawyer</p>
      <ul class="contact">
        <li>
          <svg viewBox="0 0 24 24" aria-hidden="true"><path d="M6.6 10.8c1.4 2.8 3.8 5.1 6.6 6.6l2.2-2.2c.3-.3.7-.4 1-.2 1.1.4 2.3.6 3.6.6.6 0 1 .4 1 1V20c0 .6-.4 1-1 1C10.6 21 3 13.4 3 4c0-.6.4-1 1-1h3.5c.6 0 1 .4 1 1 0 1.3.2 2.5.6 3.6.1.3 0 .7-.2 1L6.6 10.8z"/></svg>
          800-555-0147
        </li>
        <li>
          <svg viewBox="0 0 24 24" aria-hidden="true"><path d="M3 6h18v12H3z" /><path d="M3 6l9 6 9-6" fill="none" stroke="#fff" stroke-width="1.6"/></svg>
          dorian@oakpartners.example
        </li>
        <li>
          <svg viewBox="0 0 24 24" aria-hidden="true"><circle cx="12" cy="12" r="9"/><path d="M3 12h18M12 3c3 3 3 15 0 18M12 3c-3 3-3 15 0 18" fill="none" stroke="#fff" stroke-width="1.3"/></svg>
          www.oakpartners.example
        </li>
      </ul>
    </div>
  </section>

  <section class="card card-back">
    <p class="back-name">OAK PARTNERS</p>
  </section>
</body>
</html>
```